I would like to modify/update my 2 step login screen

I want a more modern looking login page for our document imaging application. I need to keep all of the same elements and buttons that currently exist. The first 2 screens are the login. The 3rd is a screenshot of the actual application home page.

```html
<!DOCTYPE html>
<html lang="en">
<head>
<meta charset="utf-8">
<title>Northfield Systems – Login Flow</title>
<link href="https://fonts.googleapis.com/css2?family=Inter:wght@400;500;600;700&display=swap" rel="stylesheet">
<style>
:root{
  --canvas:#f0f0f0;
  --page:#fafafa;
  --dark:#3b3b3d;
  --white:#ffffff;
  --ink:#2b2b2b;
  --muted:#6f6f6f;
  --faint:#9a9a9a;
  --line:#dcdcdc;
  --strip:#f4f4f4;
  --green:#4fb35a;
  --disabled:#c9c9c9;
  --focus:#5d8fd8;
  --error:#e05656;
  --link:#2f6fbe;
}
*{box-sizing:border-box;margin:0;padding:0}
html,body{width:1200px;height:482px;overflow:hidden;background:var(--canvas)}
body{font-family:"Inter",sans-serif;color:var(--ink)}
.board{position:absolute;left:0;top:0;width:2576px;height:1036px;transform:scale(0.46584);transform-origin:0 0}
.panel{position:absolute;width:797px;height:448px;background:var(--page);overflow:hidden}
.col-1{left:46px}.col-2{left:889px}.col-3{left:1733px}
.row-1{top:46px}.row-2{top:541px}
.topbar{height:131px;background:var(--dark)}
.brand{position:absolute;top:30px;left:0;width:100%;display:flex;justify-content:center;align-items:center;gap:8px}
.brand-mark{width:26px;height:26px;border-radius:50%;background:var(--white)}
.brand-name{color:var(--white);font-size:12px;font-weight:700;letter-spacing:.04em}
.card{position:absolute;left:212px;top:89px;width:373px;background:var(--white);border-radius:4px;box-shadow:0 1px 4px rgba(0,0,0,.12);overflow:hidden}
.card.step-1{height:164px}
.card.step-2{height:284px}
.card-head{height:42px;display:flex;justify-content:space-between;align-items:center;padding:0 18px;border-bottom:1px solid #eeeeee}
.card-title{font-size:14.5px;font-weight:600}
.card-step{font-size:7.5px;color:var(--muted)}
.card-step.is-error{color:var(--error)}
.field{position:absolute;left:47px;width:279px;height:25px;border:1px solid var(--line);border-radius:3px;display:flex;align-items:center;padding:0 8px;gap:7px;font-size:8px}
.field.is-focus{border-color:var(--focus);box-shadow:0 0 0 1px rgba(93,143,216,.25)}
.field.is-error{border-color:var(--error)}
.field .value{flex:1;color:var(--ink)}
.field .placeholder{flex:1;color:var(--faint)}
.field .dots{flex:1;font-size:9px;letter-spacing:.5px}
.icon{width:11px;height:11px;color:var(--muted);flex:none}
.icon-sm{width:9px;height:9px;color:var(--faint);flex:none}
.caret{display:inline-block;width:1px;height:10px;background:var(--ink);vertical-align:middle}
.btn{position:absolute;height:22px;border-radius:3px;color:var(--white);font-size:7.5px;font-weight:600;letter-spacing:.04em;display:flex;align-items:center;justify-content:center;background:var(--green)}
.btn.is-disabled{background:var(--disabled)}
.btn-next{left:276px;top:101px;width:50px}
.btn-login{left:273px;top:154px;width:53px}
.notice{position:absolute;left:0;bottom:0;width:100%;height:19px;background:var(--strip);font-size:5.6px;color:#4a4a4a;display:flex;align-items:center;justify-content:center}
.notice b{font-weight:600}
.db-row{position:absolute;left:47px;top:58px;display:flex;align-items:center;gap:8px;font-size:7.5px;color:var(--ink)}
.db-row .divider{width:1px;height:11px;background:var(--line)}
.db-row .label{color:var(--muted)}
.forgot{position:absolute;left:47px;top:160px;font-size:7.5px;font-weight:500;color:var(--link)}
.or{position:absolute;left:47px;top:187px;width:279px;display:flex;align-items:center;gap:8px;font-size:6px;color:var(--faint)}
.or::before,.or::after{content:"";flex:1;height:1px;background:#ececec}
.sso{position:absolute;left:47px;top:206px;width:279px;display:flex;gap:7px}
.sso-btn{flex:1;height:32px;border:1px solid var(--line);border-radius:3px;display:flex;align-items:center;gap:9px;padding:0 9px;font-size:6.5px;line-height:1.35;color:var(--ink)}
.sso-mark{width:10px;height:10px;background:#8a8a8a;flex:none}
.sso-mark.round{border-radius:50%;background:#222}
.foot-links{position:absolute;left:0;top:404px;width:100%;display:flex;justify-content:center;align-items:center;gap:7px;font-size:6.5px;color:#3a3a3a}
.foot-links .dot{width:2px;height:2px;border-radius:50%;background:var(--faint)}
.copyright{position:absolute;left:0;top:420px;width:100%;text-align:center;font-size:6.2px;color:var(--faint)}
</style>
</head>
<body>
<svg width="0" height="0" style="position:absolute">
  <defs>
    <symbol id="i-db" viewBox="0 0 12 12"><rect x="1.5" y="1.5" width="9" height="4" rx="1" fill="none" stroke="currentColor"/><rect x="1.5" y="6.5" width="9" height="4" rx="1" fill="none" stroke="currentColor"/></symbol>
    <symbol id="i-user" viewBox="0 0 12 12"><circle cx="6" cy="4" r="2.3" fill="none" stroke="currentColor"/><path d="M1.8 11c.5-2.3 2.2-3.5 4.2-3.5s3.7 1.2 4.2 3.5" fill="none" stroke="currentColor"/></symbol>
    <symbol id="i-lock" viewBox="0 0 12 12"><rect x="2.5" y="5.5" width="7" height="5.5" rx="1" fill="none" stroke="currentColor"/><path d="M4 5.5V3.8a2 2 0 0 1 4 0v1.7" fill="none" stroke="currentColor"/></symbol>
    <symbol id="i-clear" viewBox="0 0 12 12"><circle cx="6" cy="6" r="4.8" fill="none" stroke="currentColor"/><path d="M4.2 4.2l3.6 3.6M7.8 4.2l-3.6 3.6" stroke="currentColor"/></symbol>
    <symbol id="i-eye" viewBox="0 0 12 12"><path d="M1 6s2-3.3 5-3.3S11 6 11 6 9 9.3 6 9.3 1 6 1 6z" fill="none" stroke="currentColor"/><circle cx="6" cy="6" r="1.5" fill="none" stroke="currentColor"/><path d="M2 10L10 2" stroke="currentColor"/></symbol>
    <symbol id="i-back" viewBox="0 0 12 12"><path d="M10.5 6h-9M5 2.5L1.5 6 5 9.5" fill="none" stroke="currentColor"/></symbol>
  </defs>
</svg>

<main class="board">

  <!-- Step 1: empty -->
  <section class="panel col-1 row-1">
    <div class="topbar"></div>
    <div class="brand"><span class="brand-mark"></span><span class="brand-name">NORTHFIELD SYSTEMS</span></div>
    <div class="card step-1">
      <header class="card-head"><h1 class="card-title">Login</h1><span class="card-step">1 / 2 : Database Entry</span></header>
      <div class="field" style="top:62px"><svg class="icon"><use href="#i-db"/></svg><span class="placeholder">Database</span></div>
      <div class="btn btn-next is-disabled">NEXT</div>
      <p class="notice">All activity on this site is being recorded. Your IP Address is being saved as '<b>192.168.168.134</b>'.</p>
    </div>
    <nav class="foot-links"><span>Privacy</span><span class="dot"></span><span>Remote Support</span><span class="dot"></span><span>Contact Us</span></nav>
    <p class="copyright">Copyright 2007-2024 NS Northfield Systems</p>
  </section>

  <!-- Step 1: filled -->
  <section class="panel col-2 row-1">
    <div class="topbar"></div>
    <div class="brand"><span class="brand-mark"></span><span class="brand-name">NORTHFIELD SYSTEMS</span></div>
    <div class="card step-1">
      <header class="card-head"><h1 class="card-title">Login</h1><span class="card-step">1 / 2 : Database Entry</span></header>
      <div class="field is-focus" style="top:62px"><svg class="icon"><use href="#i-db"/></svg><span class="value">ABC12345<span class="caret"></span></span><svg class="icon-sm"><use href="#i-clear"/></svg></div>
      <div class="btn btn-next">NEXT</div>
      <p class="notice">All activity on this site is being recorded. Your IP Address is being saved as '<b>192.168.168.134</b>'.</p>
    </div>
    <nav class="foot-links"><span>Privacy</span><span class="dot"></span><span>Remote Support</span><span class="dot"></span><span>Contact Us</span></nav>
    <p class="copyright">Copyright 2007-2024 NS Northfield Systems</p>
  </section>

  <!-- Step 1: error -->
  <section class="panel col-3 row-1">
    <div class="topbar"></div>
    <div class="brand"><span class="brand-mark"></span><span class="brand-name">NORTHFIELD SYSTEMS</span></div>
    <div class="card step-1">
      <header class="card-head"><h1 class="card-title">Login</h1><span class="card-step is-error">Invalid Database</span></header>
      <div class="field is-error" style="top:62px"><svg class="icon"><use href="#i-db"/></svg><span class="value">ABC12345XYZ</span><svg class="icon-sm"><use href="#i-clear"/></svg></div>
      <div class="btn btn-next">NEXT</div>
      <p class="notice">All activity on this site is being recorded. Your IP Address is being saved as '<b>192.168.168.134</b>'.</p>
    </div>
    <nav class="foot-links"><span>Privacy</span><span class="dot"></span><span>Remote Support</span><span class="dot"></span><span>Contact Us</span></nav>
    <p class="copyright">Copyright 2007-2024 NS Northfield Systems</p>
  </section>

  <!-- Step 2: empty -->
  <section class="panel col-1 row-2">
    <div class="topbar"></div>
    <div class="brand"><span class="brand-mark"></span><span class="brand-name">NORTHFIELD SYSTEMS</span></div>
    <div class="card step-2">
      <header class="card-head"><h1 class="card-title">Login</h1><span class="card-step">2 / 2 : Username &amp; Password Entry</span></header>
      <div class="db-row"><svg class="icon"><use href="#i-back"/></svg><span class="divider"></span><svg class="icon"><use href="#i-db"/></svg><span><span class="label">Database : </span>ABC12345</span></div>
      <div class="field" style="top:84px"><svg class="icon"><use href="#i-user"/></svg><span class="placeholder">Username</span></div>
      <div class="field" style="top:114px"><svg class="icon"><use href="#i-lock"/></svg><span class="placeholder">Password</span><svg class="icon-sm"><use href="#i-eye"/></svg></div>
      <a class="forgot">Forgot Password?</a>
      <div class="btn btn-login is-disabled">LOGIN</div>
      <div class="or">OR</div>
      <div class="sso">
        <div class="sso-btn"><span class="sso-mark round"></span><span>Login with<br>Orbitly</span></div>
        <div class="sso-btn"><span class="sso-mark"></span><span>Login with<br>Quadrant</span></div>
        <div class="sso-btn"><span class="sso-mark round"></span><span>Login with<br>SingleKey</span></div>
      </div>
      <p class="notice">All activity on this site is being recorded. Your IP Address is being saved as '<b>192.168.168.134</b>'.</p>
    </div>
    <nav class="foot-links"><span>Privacy</span><span class="dot"></span><span>Remote Support</span><span class="dot"></span><span>Contact Us</span></nav>
    <p class="copyright">Copyright 2007-2024 NS Northfield Systems</p>
  </section>

  <!-- Step 2: filled -->
  <section class="panel col-2 row-2">
    <div class="topbar"></div>
    <div class="brand"><span class="brand-mark"></span><span class="brand-name">NORTHFIELD SYSTEMS</span></div>
    <div class="card step-2">
      <header class="card-head"><h1 class="card-title">Login</h1><span class="card-step">2 / 2 : Username &amp; Password Entry</span></header>
      <div class="db-row"><svg class="icon"><use href="#i-back"/></svg><span class="divider"></span><svg class="icon"><use href="#i-db"/></svg><span><span class="label">Database : </span>ABC12345</span></div>
      <div class="field" style="top:84px"><svg class="icon"><use href="#i-user"/></svg><span class="value">JohnDoe123</span><svg class="icon-sm"><use href="#i-clear"/></svg></div>
      <div class="field is-focus" style="top:114px"><svg class="icon"><use href="#i-lock"/></svg><span class="dots">●●●<span class="caret"></span></span><svg class="icon-sm"><use href="#i-eye"/></svg><svg class="icon-sm"><use href="#i-clear"/></svg></div>
      <a class="forgot">Forgot Password?</a>
      <div class="btn btn-login">LOGIN</div>
      <div class="or">OR</div>
      <div class="sso">
        <div class="sso-btn"><span class="sso-mark round"></span><span>Login with<br>Orbitly</span></div>
        <div class="sso-btn"><span class="sso-mark"></span><span>Login with<br>Quadrant</span></div>
        <div class="sso-btn"><span class="sso-mark round"></span><span>Login with<br>SingleKey</span></div>
      </div>
      <p class="notice">All activity on this site is being recorded. Your IP Address is being saved as '<b>192.168.168.134</b>'.</p>
    </div>
    <nav class="foot-links"><span>Privacy</span><span class="dot"></span><span>Remote Support</span><span class="dot"></span><span>Contact Us</span></nav>
    <p class="copyright">Copyright 2007-2024 NS Northfield Systems</p>
  </section>

  <!-- Step 2: error -->
  <section class="panel col-3 row-2">
    <div class="topbar"></div>
    <div class="brand"><span class="brand-mark"></span><span class="brand-name">NORTHFIELD SYSTEMS</span></div>
    <div class="card step-2">
      <header class="card-head"><h1 class="card-title">Login</h1><span class="card-step is-error">Invalid Username and/or Password</span></header>
      <div class="db-row"><svg class="icon"><use href="#i-back"/></svg><span class="divider"></span><svg class="icon"><use href="#i-db"/></svg><span><span class="label">Database : </span>ABC12345</span></div>
      <div class="field is-error" style="top:84px"><svg class="icon"><use href="#i-user"/></svg><span class="value">johndoe</span><svg class="icon-sm"><use href="#i-clear"/></svg></div>
      <div class="field is-error" style="top:114px"><svg class="icon"><use href="#i-lock"/></svg><span class="dots">●●●●●●</span><svg class="icon-sm"><use href="#i-eye"/></svg><svg class="icon-sm"><use href="#i-clear"/></svg></div>
      <a class="forgot">Forgot Password?</a>
      <div class="btn btn-login">LOGIN</div>
      <div class="or">OR</div>
      <div class="sso">
        <div class="sso-btn"><span class="sso-mark round"></span><span>Login with<br>Orbitly</span></div>
        <div class="sso-btn"><span class="sso-mark"></span><span>Login with<br>Quadrant</span></div>
        <div class="sso-btn"><span class="sso-mark round"></span><span>Login with<br>SingleKey</span></div>
      </div>
      <p class="notice">All activity on this site is being recorded. Your IP Address is being saved as '<b>192.168.168.134</b>'.</p>
    </div>
    <nav class="foot-links"><span>Privacy</span><span class="dot"></span><span>Remote Support</span><span class="dot"></span><span>Contact Us</span></nav>
    <p class="copyright">Copyright 2007-2024 NS Northfield Systems</p>
  </section>

</main>
</body>
</html>
```